UI/ UX Design for ERP Software

We need a new UX/UI interface for a ERP software for property managers. Our CMMS / ERP solution is made based on responsive design technologies and is coded in PHP.
The overall UX to be similar to Tev Ulna - easy navigation, intuitive menus.

Industry/Entity Type

Property Management

Number of Pages Required

5+ page

Requirements
Must have
• Round dock buttons
Consistent icons across the application
Enough Spacing between buttons/icons/ menu
Consistent Font
Nice to have
• We would like the UX to allow the users to use the application without /minimum training.
Should not have
• we don't want anything that is classic with respect to UX

```html
<!DOCTYPE html>
<html lang="en">
<head>
<meta charset="utf-8">
<title>Estatly – Property ERP</title>
<link href="https://fonts.googleapis.com/css2?family=Inter:wght@400;500;600;700&display=swap" rel="stylesheet">
<style>
:root{
  --bg-top:#ffffff;
  --bg-bottom:#f2f6fb;
  --window:#f7fafd;
  --tile:#ffffff;
  --panel:#eef4fb;
  --ink:#1b1f27;
  --muted:#4a5462;
  --value:#5b7fa6;
  --blue:#0b8af5;
  --blue-dark:#0a6fe0;
  --orange:#ff7a2d;
  --orange-dark:#f25c1f;
  --sun:#f6b300;
  --dot-y:#f7c33b;
  --dot-r:#f0504c;
  --dot-g:#35c759;
}
*{box-sizing:border-box;margin:0;padding:0}
html,body{width:1200px;height:1200px;overflow:hidden}
body{font-family:"Inter",sans-serif;color:var(--ink);
  background:linear-gradient(to bottom,var(--bg-top) 0,var(--bg-top) 327px,var(--bg-bottom) 327px)}
.window{position:absolute;left:207px;width:787px;background:var(--window);border-radius:19px;
  box-shadow:0 10px 40px rgba(30,60,110,.07)}
.window--home{top:90px;height:475px}
.window--property{top:600px;height:514px}
.traffic{position:absolute;left:24px;top:9px;display:flex;gap:5px}
.traffic span{width:6px;height:6px;border-radius:50%}
.traffic .y{background:var(--dot-y)}.traffic .r{background:var(--dot-r)}.traffic .g{background:var(--dot-g)}
.brand{position:absolute;left:24px;top:32px;display:flex;align-items:center;gap:4px;font-weight:700;font-size:12px;color:var(--blue)}
.brand i{width:13px;height:13px;background:var(--blue);border-radius:2px}
.topbar{position:absolute;right:26px;top:25px;display:flex;align-items:center;gap:12px}
.toggle{width:50px;height:20px;border-radius:10px;background:#fff;box-shadow:0 2px 6px rgba(0,0,0,.06);display:flex;align-items:center;justify-content:space-between;padding:0 5px}
.toggle .knob{width:12px;height:12px;border-radius:50%;background:var(--sun);border:2px solid #ffe07a}
.welcome{font-size:9px;color:var(--ink);margin-left:2px}
.welcome b{font-weight:600}
.avatar{width:30px;height:30px;border-radius:50%;background:linear-gradient(135deg,#5a4a42,#2d2a2c)}
.page-title{position:absolute;left:0;right:0;top:68px;text-align:center;font-size:13px;font-weight:600;letter-spacing:.2px}
.nav-panel{position:absolute;left:160px;top:91px;width:467px;height:292px;background:var(--panel);border-radius:10px}
.nav-item{position:absolute;width:70px;margin-left:-35px;text-align:center}
.nav-item .tile{width:45px;height:45px;margin:0 auto;background:var(--tile);border-radius:8px;display:flex;align-items:center;justify-content:center;box-shadow:0 3px 10px rgba(40,80,140,.06)}
.nav-item .tile svg{width:18px;height:18px}
.nav-item p{font-size:7px;margin-top:5px;color:var(--ink);white-space:nowrap}
svg{fill:none;stroke:var(--ink);stroke-width:1.4;stroke-linecap:round;stroke-linejoin:round}
.dock{position:absolute;left:331px;width:124px;height:50px;background:#fff;border-radius:10px;box-shadow:0 6px 20px rgba(30,60,110,.08);display:flex;align-items:center;justify-content:center;gap:27px}
.dock-btn{width:32px;height:32px;border-radius:9px;display:flex;align-items:center;justify-content:center}
.dock-btn--home{background:linear-gradient(160deg,var(--blue),var(--blue-dark))}
.dock-btn--apps{background:linear-gradient(160deg,var(--orange),var(--orange-dark))}
.dock-btn svg{width:14px;height:14px;stroke:none;fill:#fff}
.window--home .dock{top:407px}
.window--property .dock{top:450px}
.back-title{position:absolute;left:28px;top:67px;display:flex;align-items:center;gap:9px;font-size:14px;font-weight:600}
.back-title .back{width:13px;height:13px;border-radius:50%;background:var(--ink);display:flex;align-items:center;justify-content:center}
.back svg{width:7px;height:7px;stroke:#fff;stroke-width:2}
.photo{position:absolute;top:98px;width:125px;height:84px;border-radius:6px}
.photo--tower{left:26px;background:linear-gradient(160deg,#1e3a78 0%,#2b4f8f 45%,#6b5a3e 80%,#c08a3c 100%)}
.photo--pool{left:161px;background:linear-gradient(180deg,#8fa7c7 0%,#b7c6d9 45%,#6f7c86 60%,#3fa3d9 80%,#8f9599 100%)}
.menu-btn{position:absolute;width:125px;height:35px;background:#fff;border-radius:5px;display:flex;align-items:center;gap:9px;padding-left:11px;font-size:8.5px;font-weight:500}
.menu-btn svg{width:14px;height:14px}
.menu-btn--active{background:var(--blue);color:#fff;font-weight:600}
.menu-btn--active svg{stroke:#fff}
.info{position:absolute;left:306px;top:96px;width:455px;height:338px;background:#fff;border-radius:9px;box-shadow:0 6px 24px rgba(30,60,110,.05)}
.info h2{position:absolute;left:20px;top:15px;font-size:11px;font-weight:600}
.edit{position:absolute;right:19px;top:17px;font-size:7.5px;font-weight:600;color:var(--ink);text-decoration:underline;display:flex;align-items:center;gap:5px}
.edit svg{width:9px;height:9px;stroke:var(--blue)}
.info-col{position:absolute;top:49px}
.field{height:25.7px}
.field dt{font-size:6.8px;color:var(--ink)}
.field dd{font-size:6.8px;color:var(--value);margin-top:2px}
</style>
</head>
<body>

<section class="window window--home">
  <div class="traffic"><span class="y"></span><span class="r"></span><span class="g"></span></div>
  <div class="brand"><i></i>Estatly</div>
  <div class="topbar">
    <div class="toggle"><svg viewBox="0 0 24 24" width="12" height="12" style="stroke:var(--sun)"><circle cx="12" cy="12" r="4"/><path d="M12 2v2M12 20v2M2 12h2M20 12h2M5 5l1.5 1.5M17.5 17.5L19 19M5 19l1.5-1.5M17.5 6.5L19 5"/></svg><span class="knob"></span></div>
    <p class="welcome">Welcome, <b>Rafe Dunmore</b></p>
    <div class="avatar" role="img" aria-label="User profile photo"></div>
  </div>
  <h1 class="page-title">Start navigation</h1>
  <div class="nav-panel"></div>

  <!-- row 1 -->
  <div class="nav-item" style="left:217px;top:110px"><div class="tile"><svg viewBox="0 0 24 24"><circle cx="12" cy="8" r="4"/><path d="M4 21c1-4 4-6 8-6s7 2 8 6z"/></svg></div><p>Customers</p></div>
  <div class="nav-item" style="left:287px;top:110px"><div class="tile"><svg viewBox="0 0 24 24"><rect x="4" y="3" width="10" height="18"/><path d="M14 9h6v12H2M7 7h4M7 11h4M7 15h4"/></svg></div><p>Properties</p></div>
  <div class="nav-item" style="left:359px;top:110px"><div class="tile"><svg viewBox="0 0 24 24"><path d="M3 11l9-7 9 7M5 9v11h14V9"/><circle cx="12" cy="12" r="2"/><path d="M9 17c.5-2 5.5-2 6 0"/></svg></div><p>Tenants</p></div>
  <div class="nav-item" style="left:428px;top:110px"><div class="tile"><svg viewBox="0 0 24 24"><path d="M5 4h4l2 5-3 2c1 2 3 4 5 5l2-3 5 2v4c0 1-1 2-2 2C10 21 3 14 3 6c0-1 1-2 2-2zM15 3a6 6 0 0 1 6 6M15 7a2 2 0 0 1 2 2"/></svg></div><p>Contacts</p></div>
  <div class="nav-item" style="left:499px;top:110px"><div class="tile"><svg viewBox="0 0 24 24"><circle cx="12" cy="4" r="2"/><path d="M4 10h16M6 10v10h12V10M9 6l-2 4M15 6l2 4M9 15h6"/></svg></div><p>Contractors</p></div>
  <div class="nav-item" style="left:570px;top:110px"><div class="tile"><svg viewBox="0 0 24 24"><path d="M6 3h9l4 4v14H6z"/><circle cx="12" cy="11" r="2"/><path d="M9 17c.5-2 5.5-2 6 0"/></svg></div><p>Employees</p></div>
  <!-- row 2 -->
  <div class="nav-item" style="left:217px;top:177px"><div class="tile"><svg viewBox="0 0 24 24"><path d="M14 6a4 4 0 0 0-5 5l-6 6 3 3 6-6a4 4 0 0 0 5-5l-2 2-2-1-1-2z"/><path d="M15 15l5 5"/></svg></div><p>Maintenance</p></div>
  <div class="nav-item" style="left:287px;top:177px"><div class="tile"><svg viewBox="0 0 24 24"><rect x="4" y="5" width="16" height="16" rx="2"/><path d="M9 3h6v4H9zM7 17c0-4 2-6 5-6s5 2 5 6z"/></svg></div><p>Works orders</p></div>
  <div class="nav-item" style="left:359px;top:177px"><div class="tile"><svg viewBox="0 0 24 24"><rect x="4" y="5" width="16" height="16" rx="2"/><path d="M9 3h6v4H9zM14 11h-3a1.5 1.5 0 0 0 0 3h2a1.5 1.5 0 0 1 0 3h-3M12 9v10"/></svg></div><p>Purcharse orders</p></div>
  <div class="nav-item" style="left:428px;top:177px"><div class="tile"><svg viewBox="0 0 24 24"><circle cx="11" cy="11" r="6"/><path d="M16 16l4 4"/></svg></div><p>Inspections</p></div>
  <div class="nav-item" style="left:499px;top:177px"><div class="tile"><svg viewBox="0 0 24 24"><path d="M12 3l10 18H2zM12 10v5M12 18v.5"/></svg></div><p>Risk management</p></div>
  <div class="nav-item" style="left:570px;top:177px"><div class="tile"><svg viewBox="0 0 24 24"><circle cx="12" cy="12" r="4"/><path d="M10 12l1.5 1.5L14 11M12 2v6M12 16v6M2 12h6M16 12h6M5 5l4 4M15 15l4 4M5 19l4-4M15 9l4-4"/></svg></div><p>Compliance</p></div>
  <!-- row 3 -->
  <div class="nav-item" style="left:287px;top:242px"><div class="tile"><svg viewBox="0 0 24 24"><path d="M8 5h13v11h-8l-3 3v-3H8zM14 8v4M14 14v.5M2 8h4M3 11h3M2 14h4"/></svg></div><p>Tenant requests</p></div>
  <div class="nav-item" style="left:359px;top:242px"><div class="tile"><svg viewBox="0 0 24 24"><path d="M20 12a8 8 0 1 1-8-8" stroke-dasharray="2 3"/><path d="M15 9h-3a1.5 1.5 0 0 0 0 3h1a1.5 1.5 0 0 1 0 3h-3M12 7v10"/></svg></div><p>Budgeting</p></div>
  <div class="nav-item" style="left:428px;top:242px"><div class="tile"><svg viewBox="0 0 24 24"><circle cx="12" cy="6" r="2"/><circle cx="6" cy="16" r="2"/><circle cx="18" cy="16" r="2"/><path d="M9 10h6M3 21c0-2 6-2 6 0M15 21c0-2 6-2 6 0M8 13l2-3M16 13l-2-3"/></svg></div><p>Project mngmt</p></div>
  <div class="nav-item" style="left:499px;top:242px"><div class="tile"><svg viewBox="0 0 24 24"><path d="M13 8l4-4 4 4v5h-8zM17 13v3a4 4 0 0 1-4 4H9M4 16h5v5H4zM2 17.5h2M2 19.5h2"/></svg></div><p>Energy</p></div>
  <!-- row 4 -->
  <div class="nav-item" style="left:287px;top:310px"><div class="tile"><svg viewBox="0 0 24 24"><path d="M6 3h9l4 4v14H6zM9 17v-3M12 17v-5M15 17v-2M8 18h9"/></svg></div><p>Reports</p></div>
  <div class="nav-item" style="left:359px;top:310px"><div class="tile"><svg viewBox="0 0 24 24"><path d="M4 21h16M6 21v-5M10 21v-8M14 21v-6M18 21v-9M5 12l5-4 3 3 6-6M15 5h4v4"/></svg></div><p>Analytics</p></div>
  <div class="nav-item" style="left:428px;top:310px"><div class="tile"><svg viewBox="0 0 24 24"><path d="M3 6h18M3 12h18M3 18h18"/><circle cx="15" cy="6" r="2" fill="#fff"/><circle cx="8" cy="12" r="2" fill="#fff"/><circle cx="12" cy="18" r="2" fill="#fff"/></svg></div><p>Configuration</p></div>
  <div class="nav-item" style="left:499px;top:310px"><div class="tile"><svg viewBox="0 0 24 24"><circle cx="12" cy="12" r="3"/><path d="M12 2l2 3 3-1 1 3 3 1-1 3 3 2-3 2 1 3-3 1-1 3-3-1-2 3-2-3-3 1-1-3-3-1 1-3-3-2 3-2-1-3 3-1 1-3 3 1z"/></svg></div><p>Settings</p></div>

  <nav class="dock">
    <a class="dock-btn dock-btn--home" aria-label="Home"><svg viewBox="0 0 24 24"><path d="M12 3l9 8h-3v9h-4v-5h-4v5H6v-9H3z"/></svg></a>
    <a class="dock-btn dock-btn--apps" aria-label="All modules"><svg viewBox="0 0 24 24"><circle cx="5" cy="5" r="2"/><circle cx="12" cy="5" r="2"/><circle cx="19" cy="5" r="2"/><circle cx="5" cy="12" r="2"/><circle cx="12" cy="12" r="2"/><circle cx="19" cy="12" r="2"/><circle cx="5" cy="19" r="2"/><circle cx="12" cy="19" r="2"/><circle cx="19" cy="19" r="2"/></svg></a>
  </nav>
</section>

<section class="window window--property">
  <div class="traffic"><span class="y"></span><span class="r"></span><span class="g"></span></div>
  <div class="brand"><i></i>Estatly</div>
  <div class="topbar">
    <div class="toggle"><svg viewBox="0 0 24 24" width="12" height="12" style="stroke:var(--sun)"><circle cx="12" cy="12" r="4"/><path d="M12 2v2M12 20v2M2 12h2M20 12h2M5 5l1.5 1.5M17.5 17.5L19 19M5 19l1.5-1.5M17.5 6.5L19 5"/></svg><span class="knob"></span></div>
    <p class="welcome">Welcome, <b>Rafe Dunmore</b></p>
    <div class="avatar" role="img" aria-label="User profile photo"></div>
  </div>
  <h1 class="back-title"><span class="back"><svg viewBox="0 0 24 24"><path d="M15 5l-7 7 7 7"/></svg></span>Harbor Spire</h1>

  <div class="photo photo--tower" role="img" aria-label="Night view of the office tower"></div>
  <div class="photo photo--pool" role="img" aria-label="Residential complex with outdoor pool"></div>

  <a class="menu-btn menu-btn--active" style="left:26px;top:200px"><svg viewBox="0 0 24 24"><circle cx="12" cy="12" r="9"/><path d="M12 11v6M12 7.5v.5"/></svg>General information</a>
  <a class="menu-btn" style="left:161px;top:200px"><svg viewBox="0 0 24 24"><circle cx="12" cy="5" r="2"/><path d="M12 7v5M5 12h14M5 12v4M12 12v4M19 12v4"/><circle cx="5" cy="18" r="2"/><circle cx="12" cy="18" r="2"/><circle cx="19" cy="18" r="2"/></svg>Organization chart</a>
  <a class="menu-btn" style="left:26px;top:246px"><svg viewBox="0 0 24 24"><path d="M3 11l9-7 9 7M5 9v11h14V9"/><circle cx="12" cy="12" r="2"/><path d="M9 17c.5-2 5.5-2 6 0"/></svg>Tenant List</a>
  <a class="menu-btn" style="left:161px;top:246px"><svg viewBox="0 0 24 24"><path d="M3 11l9-7 9 7M5 9v12h14V9M14 11h-3a1.5 1.5 0 0 0 0 3h2a1.5 1.5 0 0 1 0 3h-3M12 9v10"/></svg>Property Assets</a>
  <a class="menu-btn" style="left:26px;top:292px"><svg viewBox="0 0 24 24"><circle cx="12" cy="4" r="2"/><path d="M4 10h16M6 10v10h12V10M9 6l-2 4M15 6l2 4M9 15h6"/></svg>Contractor list</a>
  <a class="menu-btn" style="left:161px;top:292px"><svg viewBox="0 0 24 24"><circle cx="12" cy="12" r="4"/><path d="M10 12l1.5 1.5L14 11M12 2v6M12 16v6M2 12h6M16 12h6M5 5l4 4M15 15l4 4M5 19l4-4M15 9l4-4"/></svg>Compliance mngmt</a>
  <a class="menu-btn" style="left:26px;top:338px"><svg viewBox="0 0 24 24"><rect x="4" y="5" width="16" height="16" rx="2"/><path d="M9 3h6v4H9zM7 17c0-4 2-6 5-6s5 2 5 6z"/></svg>Maint. Work orders</a>
  <a class="menu-btn" style="left:161px;top:338px"><svg viewBox="0 0 24 24"><rect x="4" y="5" width="16" height="16" rx="2"/><path d="M9 3h6v4H9zM14 10a3 3 0 0 0-3 4l-3 3 1.5 1.5 3-3a3 3 0 0 0 4-3"/></svg>Work orders</a>
  <a class="menu-btn" style="left:26px;top:385px"><svg viewBox="0 0 24 24"><rect x="4" y="5" width="16" height="16" rx="2"/><path d="M9 3h6v4H9zM14 11h-3a1.5 1.5 0 0 0 0 3h2a1.5 1.5 0 0 1 0 3h-3M12 9v10"/></svg>Purchase orders</a>
  <a class="menu-btn" style="left:161px;top:385px"><svg viewBox="0 0 24 24"><path d="M6 3h9l4 4v14H6zM9 12h7M9 16h7"/></svg>Files</a>

  <article class="info">
    <h2>General information</h2>
    <a class="edit"><svg viewBox="0 0 24 24"><path d="M20 14v6H4V4h6M18 3l3 3-9 9H9v-3z"/></svg>Property Edit</a>
    <dl class="info-col" style="left:24px">
      <div class="field"><dt>Province</dt><dd>Brisith Columbia</dd></div>
      <div class="field"><dt>City</dt><dd>Cedar Hollow</dd></div>
      <div class="field"><dt>Address</dt><dd>42 Quayside Lane, Northbay, BC</dd></div>
      <div class="field"><dt>GPS Addresse</dt><dd>48.7012233 : -122.9045810000003</dd></div>
      <div class="field"><dt>Postal Code</dt><dd>K4R 2P8</dd></div>
      <div class="field"><dt>Date Build</dt><dd>07/01/1980</dd></div>
      <div class="field"><dt>Area (sq.ft)</dt><dd>1500000.00</dd></div>
      <div class="field"><dt>Lot Size</dt><dd>1500000.00</dd></div>
      <div class="field"><dt>Zoning</dt><dd>CD1</dd></div>
      <div class="field"><dt>Structure type</dt><dd>Steel and concrete</dd></div>
      <div class="field"><dt>Building height</dt><dd>250 mt</dd></div>
    </dl>
    <dl class="info-col" style="left:176px">
      <div class="field"><dt>Clear height</dt><dd>45 mt</dd></div>
      <div class="field"><dt>Floor loading capacity</dt><dd>50</dd></div>
      <div class="field"><dt>Number of floors</dt><dd>30</dd></div>
      <div class="field"><dt>Number of tenants</dt><dd>30</dd></div>
      <div class="field"><dt>Suites</dt><dd>150</dd></div>
      <div class="field"><dt>Typical bay size</dt><dd>-</dd></div>
      <div class="field"><dt>Building envelope</dt><dd>None</dd></div>
      <div class="field"><dt>Parking</dt><dd>Underground + surface</dd></div>
      <div class="field"><dt>Parking ration/N. of stalls</dt><dd>6</dd></div>
      <div class="field"><dt>Sprinkler protected</dt><dd>Yes</dd></div>
      <div class="field"><dt>Sprinkler ESFR</dt><dd>No</dd></div>
    </dl>
    <dl class="info-col" style="left:308px">
      <div class="field"><dt>Sprinkler capacity (gpm)</dt><dd>No</dd></div>
      <div class="field"><dt>Fire alarm panel</dt><dd>Yes</dd></div>
      <div class="field"><dt>Fire alarm monitored</dt><dd>Yes</dd></div>
      <div class="field"><dt>Máximum electrical capacity (Amps)</dt><dd>2500</dd></div>
      <div class="field"><dt>Building back-up power source</dt><dd>Yes</dd></div>
      <div class="field"><dt>Number of elevators</dt><dd>30</dd></div>
      <div class="field"><dt>Number of escalators</dt><dd>5</dd></div>
      <div class="field"><dt>Roof construction</dt><dd>EPDM</dd></div>
      <div class="field"><dt>Roof insulation</dt><dd>-</dd></div>
      <div class="field"><dt>Utility meters</dt><dd>-</dd></div>
      <div class="field"><dt>Aditional information</dt><dd>-</dd></div>
    </dl>
  </article>

  <nav class="dock">
    <a class="dock-btn dock-btn--home" aria-label="Home"><svg viewBox="0 0 24 24"><path d="M12 3l9 8h-3v9h-4v-5h-4v5H6v-9H3z"/></svg></a>
    <a class="dock-btn dock-btn--apps" aria-label="All modules"><svg viewBox="0 0 24 24"><circle cx="5" cy="5" r="2"/><circle cx="12" cy="5" r="2"/><circle cx="19" cy="5" r="2"/><circle cx="5" cy="12" r="2"/><circle cx="12" cy="12" r="2"/><circle cx="19" cy="12" r="2"/><circle cx="5" cy="19" r="2"/><circle cx="12" cy="19" r="2"/><circle cx="19" cy="19" r="2"/></svg></a>
  </nav>
</section>

</body>
</html>
```